Business Cards for new orthopaedic surgery practice

My husband and I are starting our own orthopaedic surgery practice. We are looking for a business card that is uniform, but one will have my name/title and the other will have his. You can just create one design with my name on it for now. But when I choose your design as the winning design I will ask that you add another copy with his name/title.

We are looking for classy, simple, elite all in one. We like dark blues/a little gold/yellow. Something that goes with our logo. We want our logo incorporated. Here is all the info you need:
Business name: RV Bone & Vitality Center
Location: 38517 North Willowmere Ave
Maple Harbor, FL 33940
Phone: 954-218-4063
Fax: 954-582-7341
Email: info@myrvbonecare.example

Names: Lydia Vance, M.D.
Board Certified Hand and Upper Extremity Surgeon

Ebo Dansu, M.D.
Board Certified Hip & Knee Replacement/General Orthopaedic Surgeon

Can decide what you want to put on the back. Maybe a slogan:
Grounded in Care. Centered on You

I am just going to upload our logo. The only thing is if we select you as the winning design, the location, and phone numbers may change. We will need your help to update that once fully solidified.

Industry/Entity Type

Medical

Contact Information for Business Card

Colors
0054AA
0677BA
7BADD7
CADEEF
E8F1F8
0094D4
00A9DD
6FCCEA
C7EBF8
E9F6FB

Requirements
Must have
• class, appeal,
Should not have
• We want to air on the side of masculine if we are looking at masculine vs. feminine feel. But we still want it classy, sophisticated, and something we will love

```html
<!DOCTYPE html>
<html lang="en">
<head>
<meta charset="utf-8">
<title>RV Bone &amp; Vitality Center — Business Card</title>
<link rel="stylesheet" href="https://fonts.googleapis.com/css2?family=Cinzel:wght@400;600&family=Poppins:wght@400&display=swap">
<style>
  :root {
    --backdrop: #2b2b2d;
    --gold-light: #e6c257;
    --gold-mid: #d4a94e;
    --gold-deep: #c99f55;
    --ink: #141414;
    --navy: #1b2d63;
    --navy-deep: #16275a;
    --white: #ffffff;
    --accent-gold: #d0a658;
  }
  * { box-sizing: border-box; margin: 0; padding: 0; }
  html, body { width: 1200px; height: 689px; overflow: hidden; }
  body {
    background: var(--backdrop);
    position: relative;
    font-family: "Poppins", sans-serif;
  }
  .card {
    position: absolute;
    top: 196px;
    width: 520px;
    height: 297px;
    border-radius: 18px;
    overflow: hidden;
  }
  /* Front */
  .card-front {
    left: 50px;
    background: linear-gradient(135deg, var(--gold-light) 0%, var(--gold-mid) 55%, var(--gold-deep) 100%);
    color: var(--ink);
  }
  .front-mark {
    position: absolute;
    right: 26px;
    top: 40px;
    width: 200px;
    font-family: "Cinzel", serif;
    font-size: 26px;
    line-height: 1.25;
    text-align: center;
    color: rgba(255, 240, 200, 0.35);
  }
  .identity { position: absolute; left: 34px; top: 34px; }
  .doctor-name {
    font-family: "Cinzel", serif;
    font-weight: 600;
    font-size: 24px;
    letter-spacing: 0.5px;
  }
  .doctor-title {
    margin-top: 4px;
    font-size: 13px;
    line-height: 1.25;
    width: 250px;
  }
  .address {
    position: absolute;
    left: 34px;
    top: 150px;
    font-size: 13px;
    line-height: 1.35;
  }
  .contacts {
    position: absolute;
    left: 34px;
    top: 208px;
    list-style: none;
    font-size: 13px;
    line-height: 1.35;
  }
  .contacts li { display: flex; align-items: center; gap: 8px; }
  .contacts svg { width: 12px; height: 12px; flex: none; }
  /* Back */
  .card-back {
    left: 630px;
    background: radial-gradient(circle at 40% 40%, var(--navy) 0%, var(--navy-deep) 100%);
    color: var(--white);
  }
  .brand {
    position: absolute;
    left: 50%;
    top: 40px;
    transform: translateX(-50%);
    width: 170px;
    height: 170px;
    display: flex;
    align-items: center;
    justify-content: center;
  }
  .brand-ring { position: absolute; inset: 0; }
  .brand-name {
    font-family: "Cinzel", serif;
    font-weight: 400;
    font-size: 19px;
    line-height: 1.3;
    text-align: center;
    color: var(--white);
    width: 130px;
  }
  .slogan {
    position: absolute;
    left: 0; right: 0;
    bottom: 46px;
    text-align: center;
    font-family: "Cinzel", serif;
    font-size: 20px;
    letter-spacing: 0.5px;
  }
  .slogan-accent { color: var(--accent-gold); }
</style>
</head>
<body>
  <section class="card card-front">
    <div class="front-mark">RV Bone &amp; Vitality Center</div>
    <div class="identity">
      <h1 class="doctor-name">Lydia Vance, M.D.</h1>
      <p class="doctor-title">Board Certified Hand and Upper Extremity Surgeon</p>
    </div>
    <p class="address">38517 North Willowmere Ave<br>Maple Harbor, FL 33940</p>
    <ul class="contacts">
      <li>
        <svg viewBox="0 0 24 24" aria-hidden="true"><path fill="currentColor" d="M6.6 10.8a15 15 0 0 0 6.6 6.6l2.2-2.2a1 1 0 0 1 1-.25 11.4 11.4 0 0 0 3.6.57 1 1 0 0 1 1 1V20a1 1 0 0 1-1 1A17 17 0 0 1 3 4a1 1 0 0 1 1-1h3.5a1 1 0 0 1 1 1c0 1.25.2 2.45.57 3.57a1 1 0 0 1-.25 1z"/></svg>
        954-218-4063
      </li>
      <li>
        <svg viewBox="0 0 24 24" aria-hidden="true"><path fill="currentColor" d="M6 2h12v6H6zM3 9h18a1 1 0 0 1 1 1v8h-4v4H6v-4H2v-8a1 1 0 0 1 1-1zm5 7v4h8v-4z"/></svg>
        954-582-7341
      </li>
      <li>
        <svg viewBox="0 0 24 24" aria-hidden="true"><path fill="currentColor" d="M2 5h20v14H2zm2 2v.5l8 5 8-5V7l-8 5z"/></svg>
        info@myrvbonecare.example
      </li>
    </ul>
  </section>

  <section class="card card-back">
    <div class="brand">
      <svg class="brand-ring" viewBox="0 0 170 170" aria-hidden="true">
        <circle cx="85" cy="85" r="80" fill="none" stroke="var(--accent-gold)" stroke-width="1.5"/>
      </svg>
      <p class="brand-name">RV Bone &amp; Vitality Center</p>
    </div>
    <p class="slogan">Grounded in Care. <span class="slogan-accent">Centered on You</span></p>
  </section>
</body>
</html>
```